PSD Only - Wordpress Magazine Theme Design

We need a design for our new Premuim wordpress Magazine theme design based on our basic wire-frame. The theme will be used by people who run online magazine, news website or just blog in general.

The layout of homepage is showing recent posts in many way which is easy to user to customize the section of their homepage to show their post based on various categories.

2 Page design need (Homepage and Single Post)
Updates

Reason: want to get more designer and I am off for holiday a few days too. Better extend the time for designers as well as me also.

Target Market(s)

General Blogger who want a nice premium theme as well as other content based wesite.

Industry/Entity Type

Online

Font styles to use
Sans Serif

Requirements
Must have
• + Must have 2 page design based on Wireframing. Homepage (home.png) annd Single Post (Single.png)
• + Layout must be based on wireframe.
• + Width 1025px
• + 2 Navigation Menu in Header Must be in different style. When theme goes public, user can choose to have both or only 1 navigation or completely hide both of them.
• + 2 Featured Content Slider as you see in wire-frame. They must be in different style from each other.
• + Those recent news section is only about arrange post in defferent ways which only include post feature image, post title as well as post meta info.
• + Sidebar Widget Must be 300px (not include margin or padding) in order to be able for user to place ads with (300px of width) in sidebar widget)
• + Footer Widget Section should have a bit different colour in order to look different for main layout.
Nice to have
• + Drop down Menu
• + (Optional) Some custom Widget (Based on your imagination and creativity)

```html
<!DOCTYPE html>
<html lang="en">
<head>
<meta charset="utf-8">
<title>Kite Magazine — Home</title>
<link href="https://fonts.googleapis.com/css2?family=Open+Sans:wght@400;600;700&display=swap" rel="stylesheet">
<style>
:root{
  --blue:#1b4c96;
  --blue-dark:#0f3772;
  --blue-panel:#1d5cab;
  --heading:#1d4f91;
  --ink:#333;
  --muted:#8a8a8a;
  --rule:#dcdcdc;
  --side-bg:#eeeeee;
  --topbar:#2a2a2a;
  --footer:#1e1e1e;
  --footer-widgets:#e6e6e6;
  --green:#7ba23a;
  --btn:#3b3b3b;
}
*{box-sizing:border-box;margin:0;padding:0}
html,body{width:1200px;height:4235px;overflow:hidden}
body{position:relative;background:#fff;font-family:"Open Sans",Arial,sans-serif;color:var(--ink)}
.abs{position:absolute}
.ph{display:block}
/* top bar */
.topbar{left:0;top:0;width:1200px;height:40px;background:var(--topbar)}
.topbar .menu{position:absolute;left:99px;top:0;display:flex;height:40px}
.topbar .menu a{color:#cfcfcf;font-size:11px;text-transform:uppercase;text-decoration:none;padding:0 16px;line-height:40px}
.topbar .menu a.active{background:#111;color:#fff}
.social-top{position:absolute;right:99px;top:0;display:flex}
.social-top span{width:58px;height:40px;border-left:1px solid #444;display:flex;align-items:center;justify-content:center}
.social-top span i{width:14px;height:14px;background:#bbb;border-radius:2px;display:block}
/* header */
.logo{left:99px;top:56px}
.logo .name{font-size:40px;font-weight:600;color:var(--heading);line-height:1}
.logo .tag{font-size:10px;color:var(--muted);margin-top:6px}
.header-ad{left:474px;top:56px;width:627px;height:74px;background:linear-gradient(90deg,#e9f3d2 0%,#8cc63f 40%,#3e8e1e 100%)}
/* nav */
.mainnav{left:0;top:141px;width:1200px;height:43px;background:var(--blue)}
.mainnav .menu{position:absolute;left:99px;top:0;display:flex}
.mainnav .menu a{color:#fff;font-size:11px;text-transform:uppercase;text-decoration:none;padding:0 18px;line-height:43px}
.mainnav .menu a.active{background:var(--blue-dark)}
.search{position:absolute;left:884px;top:9px;width:217px;height:26px;background:#fff;display:flex;align-items:center;justify-content:space-between;padding:0 8px;font-size:11px;color:#999}
/* hero */
.hero{left:0;top:192px;width:1200px;height:466px;background:linear-gradient(120deg,#6e5a4a 0%,#c79a7a 35%,#e6d2c0 55%,#7b8fa3 80%,#3f4d5c 100%)}
.hero-cap{position:absolute;background:rgba(0,0,0,.65);color:#fff;font-size:19px;padding:0 14px;height:43px;line-height:43px;white-space:nowrap}
.arrow{position:absolute;width:22px;height:34px;background:rgba(0,0,0,.4);display:flex;align-items:center;justify-content:center}
/* featured slider 2 */
.slide2{left:99px;top:700px;width:714px;height:316px;display:flex}
.slide2 .img{width:511px;height:316px;background:linear-gradient(160deg,#8fc5e8 0%,#bfe0f2 45%,#e7d8b3 75%,#c9b38a 100%)}
.slide2 .panel{width:203px;background:var(--blue-panel);color:#fff;padding:58px 18px 0 18px}
.slide2 h3{font-size:14px;font-weight:700;line-height:1.35;margin-bottom:12px}
.slide2 p{font-size:10px;line-height:1.5;color:#dce7f6}
/* section headings */
.sec-title{font-size:21px;font-weight:600;color:var(--heading)}
.rule{height:1px;background:var(--rule)}
.meta{font-size:10px;color:#555}
.post-title{font-size:11px;font-weight:700;color:#222}
.excerpt{font-size:9.5px;line-height:1.45;color:var(--muted)}
/* grid of three */
.three{display:flex;gap:30px}
.three .card{width:220px}
.three .thumb{width:220px;height:124px}
.three .post-title{margin:10px 0 4px}
/* two */
.two{display:flex;gap:30px}
.two .card{width:345px}
.two .thumb{width:345px;height:189px}
.two .post-title{margin:12px 0 4px}
/* list grid */
.listgrid{display:grid;grid-template-columns:345px 345px;column-gap:30px;row-gap:30px}
.litem{display:flex;gap:12px}
.litem .thumb{width:90px;height:85px;flex:none}
.litem .post-title{margin-bottom:4px}
/* wide list */
.wide{display:flex;gap:18px}
.wide .thumb{width:192px;height:124px;flex:none}
.wide .post-title{margin:6px 0 8px}
/* big posts */
.big .thumb{width:714px;height:240px}
.big h3{font-size:15px;font-weight:400;color:#222;line-height:1.45;margin:18px 0 12px}
.big .excerpt{font-size:10.5px;margin-bottom:14px}
.readmore{display:inline-block;background:var(--btn);color:#fff;font-size:10px;padding:0 10px;height:28px;line-height:28px;margin-top:16px}
/* pagination */
.pager{display:flex;gap:10px}
.pager span{width:28px;height:28px;border-radius:50%;background:#e1e1e1;color:#555;font-size:10px;display:flex;align-items:center;justify-content:center}
.pager span.on{background:var(--blue);color:#fff}
/* sidebar */
.widget{width:260px;background:var(--side-bg)}
.widget .whead{background:var(--blue);color:#fff;font-size:14px;font-weight:600;padding:0 14px;height:42px;line-height:42px}
.widget .wbody{padding:14px 14px 0}
.widget .viewall{font-size:9px;font-weight:700;color:#555;padding:10px 14px 12px;border-top:1px solid #d5d5d5;margin-top:6px}
.recent-item{padding:8px 0 14px;border-bottom:1px solid #d5d5d5}
.recent-item:last-child{border-bottom:none}
.recent-item .post-title{margin-bottom:6px;line-height:1.35}
.cat-list{list-style:none}
.cat-list li{font-size:10.5px;color:#444;padding:8px 0 8px 14px;border-bottom:1px solid #dcdcdc;position:relative}
.cat-list li:before{content:"";position:absolute;left:2px;top:14px;width:4px;height:4px;background:#999;border-radius:50%}
.pop-item{display:flex;gap:10px;padding:6px 0 14px;border-bottom:1px solid #d5d5d5}
.pop-item:last-child{border-bottom:none}
.pop-item .thumb{width:72px;height:82px;flex:none}
.side-ad{left:841px;top:2132px;width:260px;height:211px;background:linear-gradient(135deg,#fff 0%,#f2f2f2 45%,#d92a2a 100%);display:flex;align-items:flex-end;justify-content:center;padding-bottom:18px}
.side-ad span{font-size:34px;font-weight:700;color:#c0161b}
/* footer widgets */
.fwidgets{left:0;top:3727px;width:1200px;height:282px;background:var(--footer-widgets)}
.fbox{position:absolute;top:8px;width:302px;height:262px;background:#fff}
.fbox h4{font-size:15px;font-weight:700;color:var(--green);text-transform:uppercase;text-align:center;padding:18px 0 12px;letter-spacing:.3px}
.gal{display:grid;grid-template-columns:repeat(3,78px);gap:10px;justify-content:center}
.gal i{display:block;height:62px;background:linear-gradient(135deg,#2d2d38,#6b6b7a)}
.fans{display:grid;grid-template-columns:repeat(6,38px);gap:6px 6px;justify-content:center;padding:6px 12px;border:1px solid #ddd;margin:0 18px}
.fans i{display:block;height:38px;background:linear-gradient(135deg,#caa68c,#7a6a5e)}
.tweet{margin:0 18px;border:1px solid #ddd;padding:10px;font-size:9px;color:#666;line-height:1.5;height:150px}
.tweet b{color:var(--blue)}
.tweet-actions{color:var(--blue)}
.tweet-actions span{margin-right:8px}
.tweet-input{margin:6px 18px 0;border:1px solid #ddd;height:26px;font-size:9px;color:#aaa;padding:6px 10px}
/* footer */
.footer{left:0;top:4043px;width:1200px;height:192px;background:var(--footer)}
.fbtns{position:absolute;left:113px;top:34px;display:flex;gap:48px}
.fbtn{width:216px;height:45px;color:#fff;font-size:13px;line-height:1.25;display:flex;align-items:center;justify-content:space-between;padding:0 12px}
.fbtn i{width:28px;height:28px;background:rgba(255,255,255,.85);border-radius:3px;display:block;flex:none;margin-left:8px}
.flinks{position:absolute;left:0;width:1200px;top:116px;text-align:center;font-size:10px;color:#888}
.flinks span{margin:0 8px}
.copy{position:absolute;left:0;width:1200px;top:148px;text-align:center;font-size:10px;color:#888}
</style>
</head>
<body>

<!-- top bar -->
<div class="abs topbar">
  <nav class="menu"><a class="active">Home</a><a>About us</a><a>Resources</a><a>Contact us</a></nav>
  <div class="social-top"><span><i></i></span><span><i></i></span><span><i></i></span><span><i></i></span></div>
</div>

<!-- header -->
<div class="abs logo"><div class="name">Kite Magazine</div><div class="tag">Aliquam dignissim elit nec mauris</div></div>
<div class="abs header-ad ph" role="img" aria-label="Hostwell web hosting advertisement banner"></div>

<div class="abs mainnav">
  <nav class="menu"><a class="active">Home</a><a>About us</a><a>Resources</a><a>Contact us</a></nav>
  <div class="search">Search
    <svg width="12" height="12" viewBox="0 0 12 12"><circle cx="5" cy="5" r="3.8" fill="none" stroke="#555" stroke-width="1.5"/><line x1="8" y1="8" x2="11" y2="11" stroke="#555" stroke-width="1.5"/></svg>
  </div>
</div>

<!-- hero slider -->
<div class="abs hero ph" role="img" aria-label="Group of friends in sunglasses laughing together">
  <div class="arrow" style="left:0;top:216px"><svg width="8" height="12"><path d="M7 1L2 6l5 5" stroke="#fff" stroke-width="2" fill="none"/></svg></div>
  <div class="arrow" style="right:0;top:216px"><svg width="8" height="12"><path d="M1 1l5 5-5 5" stroke="#fff" stroke-width="2" fill="none"/></svg></div>
  <div class="hero-cap" style="left:725px;top:319px;width:368px">Proin ut enim blandit, egestas libero</div>
  <div class="hero-cap" style="left:864px;top:370px;width:229px">Aliquam dignissim elit</div>
</div>

<!-- featured slider 2 -->
<div class="abs slide2">
  <div class="img ph" role="img" aria-label="Three friends jumping on a beach"></div>
  <div class="panel">
    <h3>Praesent iaculis fauci bus urna sit amet</h3>
    <p>Mauris sed erat velit. Nulla facilisi. Donec sit amet lectus vel ante congue feugiat at quis diam. Sed nisi porta, lorem ut accumsan dapibus, nunc erat tincidunt metus, vel malesuada nibh lorem at nisi. Cras porta vel tortor a cursus.</p>
  </div>
  <div class="arrow" style="left:6px;top:141px;background:none"><svg width="10" height="16"><path d="M8 1L2 8l6 7" stroke="#fff" stroke-width="2" fill="none"/></svg></div>
  <div class="arrow" style="left:483px;top:141px;background:none"><svg width="10" height="16"><path d="M2 1l6 7-6 7" stroke="#fff" stroke-width="2" fill="none"/></svg></div>
</div>

<!-- section: three cards -->
<div class="abs sec-title" style="left:99px;top:1038px">Mauris tellus metus</div>
<div class="abs three" style="left:99px;top:1076px">
  <div class="card"><div class="thumb ph" role="img" aria-label="Man in a jacket outdoors" style="background:linear-gradient(135deg,#3a4a3c,#8a8d7a)"></div><div class="post-title">Proin a dolor mauris</div><div class="excerpt">Donec molestie nisi et tellus hendrerit ultricies. Nunc eu ligula sed ipsum pulvinar mattis.</div><div class="meta" style="margin-top:4px">Apr 12, 2015</div></div>
  <div class="card"><div class="thumb ph" role="img" aria-label="Tropical bay with boats" style="background:linear-gradient(160deg,#3fa9d8,#9bd3a8,#e8dcb0)"></div><div class="post-title">Proin a dolor mauris</div><div class="excerpt">Donec molestie nisi et tellus hendrerit ultricies. Nunc eu ligula sed ipsum pulvinar mattis.</div><div class="meta" style="margin-top:4px">Apr 12, 2015</div></div>
  <div class="card"><div class="thumb ph" role="img" aria-label="Friends toasting at a party" style="background:linear-gradient(135deg,#5a1e12,#c96a2d,#2a1a12)"></div><div class="post-title">Proin a dolor mauris</div><div class="excerpt">Donec molestie nisi et tellus hendrerit ultricies. Nunc eu ligula sed ipsum pulvinar mattis.</div><div class="meta" style="margin-top:4px">Apr 12, 2015</div></div>
</div>
<div class="abs rule" style="left:99px;top:1321px;width:714px"></div>

<!-- section: two cards -->
<div class="abs sec-title" style="left:99px;top:1346px">Aliquam pulvinar nulla</div>
<div class="abs two" style="left:99px;top:1392px">
  <div class="card"><div class="thumb ph" role="img" aria-label="Players around a casino table" style="background:linear-gradient(135deg,#1a1410,#6b4a2a,#2a1f18)"></div><div class="post-title">Proin a dolor mauris</div><div class="excerpt">Donec molestie nisi et tellus hendrerit ultricies. Nunc eu ligula sed ipsum pulvinar mattis, quis aliquet sapien.</div><div class="meta" style="margin-top:4px">Apr 12, 2015</div></div>
  <div class="card"><div class="thumb ph" role="img" aria-label="Rows of lit slot machines" style="background:linear-gradient(135deg,#3a2008,#d8a040,#4a2a10)"></div><div class="post-title">Proin a dolor mauris</div><div class="excerpt">Donec molestie nisi et tellus hendrerit ultricies. Nunc eu ligula sed ipsum pulvinar mattis, quis aliquet sapien.</div><div class="meta" style="margin-top:4px">Apr 12, 2015</div></div>
</div>
<div class="abs rule" style="left:99px;top:1694px;width:714px"></div>

<!-- section: list grid -->
<div class="abs sec-title" style="left:99px;top:1727px">Nam et turpis</div>
<div class="abs listgrid" style="left:99px;top:1770px">
  <div class="litem"><div class="thumb ph" role="img" aria-label="Couple outdoors" style="background:linear-gradient(135deg,#c7b08a,#6f8a5a)"></div><div><div class="post-title">Maecenas sed nibh sed</div><div class="excerpt">Sed elementum odio nunc, gravida mattis lorem interdum tempor. Suspendisse gravida neque.</div><div class="meta" style="margin-top:6px">Apr 12, 2015</div></div></div>
  <div class="litem"><div class="thumb ph" role="img" aria-label="Woman in warm light" style="background:linear-gradient(135deg,#6a3a2a,#d49a6a)"></div><div><div class="post-title">Maecenas sed nibh sed</div><div class="excerpt">Sed elementum odio nunc, gravida mattis lorem interdum tempor. Suspendisse gravida neque.</div><div class="meta" style="margin-top:6px">Apr 12, 2015</div></div></div>
  <div class="litem"><div class="thumb ph" role="img" aria-label="Motocross rider" style="background:linear-gradient(135deg,#e8eef4,#3b6fa8)"></div><div><div class="post-title">Maecenas sed nibh sed</div><div class="excerpt">Sed elementum odio nunc, gravida mattis lorem interdum tempor. Suspendisse gravida neque.</div><div class="meta" style="margin-top:6px">Apr 12, 2015</div></div></div>
  <div class="litem"><div class="thumb ph" role="img" aria-label="Person reading a book" style="background:linear-gradient(135deg,#d8c0a8,#8a6a5a)"></div><div><div class="post-title">Maecenas sed nibh sed</div><div class="excerpt">Sed elementum odio nunc, gravida mattis lorem interdum tempor. Suspendisse gravida neque.</div><div class="meta" style="margin-top:6px">Apr 12, 2015</div></div></div>
  <div class="litem"><div class="thumb ph" role="img" aria-label="Man in a suit" style="background:linear-gradient(135deg,#3a3a2e,#7a8a5a)"></div><div><div class="post-title">Maecenas sed nibh sed</div><div class="excerpt">Sed elementum odio nunc, gravida mattis lorem interdum tempor. Suspendisse gravida neque.</div><div class="meta" style="margin-top:6px">Apr 12, 2015</div></div></div>
  <div class="litem"><div class="thumb ph" role="img" aria-label="Dark sports car" style="background:linear-gradient(135deg,#1a1a1a,#7a7a7a)"></div><div><div class="post-title">Maecenas sed nibh sed</div><div class="excerpt">Sed elementum odio nunc, gravida mattis lorem interdum tempor. Suspendisse gravida neque.</div><div class="meta" style="margin-top:6px">Apr 12, 2015</div></div></div>
</div>
<div class="abs rule" style="left:99px;top:2128px;width:714px"></div>

<!-- section: wide list -->
<div class="abs sec-title" style="left:99px;top:2162px">Fusce eget neque elit</div>
<div class="abs" style="left:99px;top:2211px;width:714px">
  <div class="wide"><div class="thumb ph" role="img" aria-label="Highway traffic at dusk" style="background:linear-gradient(160deg,#5a8ab8,#b8c8d0,#6a6a5a)"></div><div><div class="post-title">Proin a dolor mauris</div><div class="excerpt">Quisque aliquet ex nec vestibulum pulvinar. Pellentesque convallis molestie enim an amet efficitur. Etiam id imperdiet lectus. Vivamus lacus justo, ultrices nec erat in, euismod iaculis mauris. Vivamus quis mauris at nisl scelerisque sagittis. Nunc tempus nunc ipsum, tincidunt lectus hendrerit in. Nullam efficitur ipsum sit.</div><div class="meta" style="margin-top:8px">Post in : Category &nbsp;|&nbsp; Post by : Mark Dalton &nbsp;|&nbsp; Apr 12, 2015</div></div></div>
  <div class="wide" style="margin-top:31px"><div class="thumb ph" role="img" aria-label="Cable-stayed bridge under blue sky" style="background:linear-gradient(180deg,#4a8ad0,#a8c8e8,#5a6a7a)"></div><div><div class="post-title">Proin a dolor mauris</div><div class="excerpt">Quisque aliquet ex nec vestibulum pulvinar. Pellentesque convallis molestie enim an amet efficitur. Etiam id imperdiet lectus. Vivamus lacus justo, ultrices nec erat in, euismod iaculis mauris. Vivamus quis mauris at nisl scelerisque sagittis. Nunc tempus nunc ipsum, tincidunt lectus hendrerit in. Nullam efficitur ipsum sit.</div><div class="meta" style="margin-top:8px">Post in : Category &nbsp;|&nbsp; Post by : Mark Dalton &nbsp;|&nbsp; Apr 12, 2015</div></div></div>
</div>
<div class="abs rule" style="left:99px;top:2534px;width:714px"></div>

<!-- section: big posts -->
<div class="abs sec-title" style="left:99px;top:2563px">Nunc sit amet consequat risus</div>
<div class="abs big" style="left:99px;top:2617px;width:714px">
  <div class="thumb ph" role="img" aria-label="Couple relaxing under a colourful beach umbrella" style="background:linear-gradient(135deg,#f0c040,#e86a8a,#f6e2b0,#8ac0d8)"></div>
  <h3>Integer eu massa lacinia, lacinia nulla non, volutpat purus. Sed libero felis, vestibulum et dolor eget, lacinia aliquet neque.</h3>
  <div class="excerpt">Pellentesque convallis molestie enim an amet efficitur. Etiam id imperdiet lectus. Vivamus lacus justo, ultrices nec erat in, euismod iaculis mauris. Vivamus quis mauris at nisl scelerisque sagittis. Nunc tempus nunc ipsum, tincidunt lectus hendrerit in. Aenean placerat, nibh vel accumsan aliquet, magna nibh accumsan nibh, ac tempus nunc ipsum ac tellus. Cras augue magna, placerat eget odio non, congue suscipit neque.</div>
  <div class="meta">Post in : Category &nbsp;|&nbsp; Post by : Mark Dalton &nbsp;|&nbsp; Apr 12, 2015</div>
  <div class="readmore">Read more</div>
</div>
<div class="abs big" style="left:99px;top:3123px;width:714px">
  <div class="thumb ph" role="img" aria-label="Man standing in a neon-lit city square at night" style="background:linear-gradient(135deg,#1a2a6a,#c8306a,#3a6ad8,#141830)"></div>
  <h3>Integer eu massa lacinia, lacinia nulla non, volutpat purus. Sed libero felis, vestibulum et dolor eget, lacinia aliquet neque.</h3>
  <div class="excerpt">Pellentesque convallis molestie enim an amet efficitur. Etiam id imperdiet lectus. Vivamus lacus justo, ultrices nec erat in, euismod iaculis mauris. Vivamus quis mauris at nisl scelerisque sagittis. Nunc tempus nunc ipsum, tincidunt lectus hendrerit in. Aenean placerat, nibh vel accumsan aliquet, magna nibh accumsan nibh, ac tempus nunc ipsum ac tellus. Cras augue magna, placerat eget odio non, congue suscipit neque.</div>
  <div class="meta">Post in : Category &nbsp;|&nbsp; Post by : Mark Dalton &nbsp;|&nbsp; Apr 12, 2015</div>
  <div class="readmore">Read more</div>
</div>
<div class="abs rule" style="left:99px;top:3623px;width:714px"></div>
<div class="abs pager" style="left:577px;top:3656px"><span class="on">1</span><span>2</span><span>3</span><span>4</span><span>5</span><span>&raquo;</span></div>

<!-- sidebar -->
<div class="abs widget" style="left:841px;top:700px;height:463px">
  <div class="whead">Recent Post</div>
  <div class="wbody">
    <div class="recent-item"><div class="post-title">Etiam mattis augue vehicula odio posuere amet tempus</div><div class="excerpt">Fusce vitae lacus id ante in pulvinar maximus. Aenean placerat, nibh vel aliquet, magna nibh accumsan.</div></div>
    <div class="recent-item"><div class="post-title">Etiam mattis augue vehicula odio posuere amet tempus</div><div class="excerpt">Fusce vitae lacus id ante in pulvinar maximus. Aenean placerat, nibh vel aliquet, magna nibh accumsan.</div></div>
    <div class="recent-item"><div class="post-title">Etiam mattis augue vehicula odio posuere amet tempus</div><div class="excerpt">Fusce vitae lacus id ante in pulvinar maximus. Aenean placerat, nibh vel aliquet, magna nibh accumsan.</div></div>
  </div>
  <div class="viewall">VIEW ALL</div>
</div>

<div class="abs widget" style="left:841px;top:1186px;height:460px">
  <div class="whead">Category</div>
  <div class="wbody" style="padding-top:4px">
    <ul class="cat-list">
      <li>Aliquam ac elit vitae</li><li>Nulla ut neque</li><li>Nam ultrices orci</li><li>Proin ut enim blandit</li><li>Donec aliquam</li><li>Nunc pellentesque</li><li>Aliquam dignissim</li><li>Nulla porttitor nibh ut</li><li>Nam tempus</li><li>Duis hendrerit arcu</li><li>Pellentesque</li><li>Nam elementum velit</li>
    </ul>
  </div>
  <div class="viewall" style="border-top:none;margin-top:0">VIEW ALL</div>
</div>

<div class="abs widget" style="left:841px;top:1666px;height:437px">
  <div class="whead">Most Popular Post</div>
  <div class="wbody" style="padding-top:8px">
    <div class="pop-item"><div class="thumb ph" role="img" aria-label="Friends smiling outdoors" style="background:linear-gradient(135deg,#8a5a3a,#d8b08a)"></div><div><div class="post-title">Maecenas sed nibh sed</div><div class="excerpt">Sed elementum odio nunc, gravida mattis lorem interdum tempor.</div><div class="meta" style="margin-top:6px">Apr 12, 2015</div></div></div>
    <div class="pop-item"><div class="thumb ph" role="img" aria-label="Friends jumping on a beach" style="background:linear-gradient(160deg,#8fc5e8,#e7d8b3)"></div><div><div class="post-title">Maecenas sed nibh sed</div><div class="excerpt">Sed elementum odio nunc, gravida mattis lorem interdum tempor.</div><div class="meta" style="margin-top:6px">Apr 12, 2015</div></div></div>
    <div class="pop-item"><div class="thumb ph" role="img" aria-label="Person standing in a green field" style="background:linear-gradient(160deg,#c8d8e8,#5a8a3a)"></div><div><div class="post-title">Maecenas sed nibh sed</div><div class="excerpt">Sed elementum odio nunc, gravida mattis lorem interdum tempor.</div><div class="meta" style="margin-top:6px">Apr 12, 2015</div></div></div>
  </div>
  <div class="viewall" style="margin-top:0">VIEW ALL</div>
</div>

<div class="abs side-ad ph" role="img" aria-label="Music single advertisement for Nova Beat"><span>NOVA BEAT</span></div>

<!-- footer widgets -->
<div class="abs fwidgets">
  <div class="fbox" style="left:113px">
    <h4>Snapgram Gallery</h4>
    <div class="gal"><i role="img" aria-label="Gallery photo"></i><i role="img" aria-label="Gallery photo"></i><i role="img" aria-label="Gallery photo"></i><i role="img" aria-label="Gallery photo"></i><i role="img" aria-label="Gallery photo"></i><i role="img" aria-label="Gallery photo"></i></div>
    <div style="text-align:center;margin-top:14px"><svg width="30" height="12"><path d="M7 2L3 6l4 4M23 2l4 4-4 4" stroke="#555" stroke-width="1.6" fill="none"/></svg></div>
  </div>
  <div class="fbox" style="left:449px">
    <h4>Find us on Facepage</h4>
    <div class="fans"><i></i><i></i><i></i><i></i><i></i><i></i><i></i><i></i><i></i><i></i><i></i><i></i><i></i><i></i><i></i><i></i><i></i><i></i></div>
    <div style="margin:8px 18px 0;font-size:9px;color:#666">1,245 readers follow this page</div>
  </div>
  <div class="fbox" style="left:785px">
    <h4>Follow us on Chirper</h4>
    <div class="tweet"><b>Mark Dalton</b> @kitemag<br>Nulla tincidunt elit a mauris pulvinar molestie. Maecenas vel nunc vitae dui mollis auctor. Proin id dolor eu urna sagittis fringilla. Nulla suscipit felis eget tempus tellus feugiat, ut sem libero congue. Cras quam nisi euismod.<br><br><div class="tweet-actions"><span>Answer</span><span>Share</span><span>Save</span><span>More</span></div></div>
    <div class="tweet-input">Write a new message</div>
  </div>
</div>

<!-- footer -->
<div class="abs footer">
  <div class="fbtns">
    <div class="fbtn" style="background:#3b5998">Find us on Facepage<i></i></div>
    <div class="fbtn" style="background:#2aa3d8">Follow us on Chirper<i></i></div>
    <div class="fbtn" style="background:#d6392b">Connect with us on Circles+<i></i></div>
    <div class="fbtn" style="background:#f07f1f">Know about us on RSS<i></i></div>
  </div>
  <div class="flinks"><span>Home</span>|<span>About us</span>|<span>Resources</span>|<span>Contact us</span></div>
  <div class="copy">Copyright © 2015 Kite Magazine. All rights reserved.</div>
</div>

</body>
</html>
```